BUSINESS CARD DESIGN

NAME- DALE VORSKIN
PHONE NUMER - 555- 714-9082
EMAIL- OFFICE@TRV-GROUNDMAKRZ.COM
BACK OF CARD- SPEACIALIZES IN LAND CLEARING, FORESTRY MUCLHING AND EXCAVATION

Contact Information for Business Card

NAME- DALE VORSKIN PHONE NUMER - 555- 714-9082 EMAIL- OFFICE@TRV-GROUNDMAKRZ.COM BACK OF CARD- SPEACIALIZES IN LAND CLEARING , MUCLHING AND EXCAVATION

```html
<!DOCTYPE html>
<html lang="en">
<head>
<meta charset="utf-8">
<title>Trevane Groundmakrz LLC – Business Card</title>
<link rel="stylesheet" href="https://fonts.googleapis.com/css2?family=Montserrat:wght@400;500;700&display=swap">
<style>
  :root {
    --backdrop: #5e4c38;
    --card: #0b0b0b;
    --gold: #f5b41c;
    --white: #f2f2f2;
    --emboss: #1d1d1d;
    --emboss-text: #2a2a2a;
  }
  html, body {
    margin: 0;
    padding: 0;
    overflow: hidden;
  }
  body {
    width: 900px;
    height: 1200px;
    background: var(--backdrop);
    position: relative;
    font-family: "Montserrat", sans-serif;
  }
  .card {
    position: absolute;
    left: 80px;
    width: 742px;
    height: 442px;
    background: var(--card);
    border-radius: 24px;
    overflow: hidden;
  }
  .card--front { top: 130px; }
  .card--back { top: 638px; }

  /* Front: company name block */
  .brand {
    position: absolute;
    left: 40px;
    top: 22px;
    width: 265px;
    display: flex;
    flex-direction: column;
    align-items: center;
    gap: 14px;
  }
  .brand__dot {
    width: 130px;
    height: 130px;
    border-radius: 50%;
    background: var(--gold);
  }
  .brand__name {
    margin: 0;
    color: var(--gold);
    font-weight: 700;
    font-size: 20px;
    letter-spacing: 1px;
    text-align: center;
    line-height: 1.25;
  }

  /* Front: person */
  .person {
    position: absolute;
    right: 49px;
    top: 46px;
    text-align: right;
  }
  .person__name {
    margin: 0;
    color: var(--gold);
    font-weight: 700;
    font-size: 25px;
    letter-spacing: 0.5px;
  }
  .person__title {
    margin: 4px 0 0;
    color: var(--white);
    font-size: 16px;
    font-weight: 400;
  }

  /* Front: contacts */
  .contacts {
    position: absolute;
    left: 40px;
    top: 321px;
    margin: 0;
    padding: 0;
    list-style: none;
  }
  .contacts li {
    display: flex;
    align-items: center;
    gap: 9px;
    height: 28px;
    color: var(--white);
    font-size: 15.5px;
  }
  .contacts svg { width: 15px; height: 15px; fill: var(--gold); }

  /* Front: faint decorative circle */
  .front-mark {
    position: absolute;
    left: 412px;
    top: 168px;
    width: 290px;
    height: 250px;
    border-radius: 50%;
    background: var(--emboss);
  }

  /* Back */
  .back-lockup {
    position: absolute;
    left: 0;
    right: 0;
    top: 80px;
    display: flex;
    flex-direction: column;
    align-items: center;
  }
  .back-lockup__dot {
    width: 200px;
    height: 175px;
    border-radius: 50%;
    background: var(--emboss);
  }
  .back-lockup__name {
    margin: 22px 0 0;
    color: var(--emboss-text);
    font-weight: 700;
    font-size: 30px;
    letter-spacing: 1px;
    line-height: 1.2;
    text-align: center;
  }
  .back-lockup__services {
    margin: 16px 0 0;
    color: var(--emboss-text);
    font-weight: 500;
    font-size: 14px;
    letter-spacing: 2px;
    text-transform: uppercase;
    text-align: center;
  }
</style>
</head>
<body>

<section class="card card--front">
  <div class="brand">
    <div class="brand__dot"></div>
    <p class="brand__name">TREVANE<br>GROUNDMAKRZ LLC</p>
  </div>

  <div class="person">
    <h1 class="person__name">DALE VORSKIN</h1>
    <p class="person__title">Managing Director</p>
  </div>

  <div class="front-mark" aria-hidden="true"></div>

  <ul class="contacts">
    <li>
      <svg viewBox="0 0 24 24"><path d="M6.6 10.8a15.1 15.1 0 0 0 6.6 6.6l2.2-2.2a1 1 0 0 1 1-.25 11.4 11.4 0 0 0 3.6.57 1 1 0 0 1 1 1V20a1 1 0 0 1-1 1A17 17 0 0 1 3 4a1 1 0 0 1 1-1h3.5a1 1 0 0 1 1 1c0 1.25.2 2.45.57 3.57a1 1 0 0 1-.25 1z"/></svg>
      555- 714-9082
    </li>
    <li>
      <svg viewBox="0 0 24 24"><path d="M2 6l10 6 10-6V5H2zM2 8v11h20V8l-10 6z"/></svg>
      OFFICE@TRV-GROUNDMAKRZ.COM
    </li>
    <li>
      <svg viewBox="0 0 24 24"><path d="M12 2a10 10 0 1 0 0 20 10 10 0 0 0 0-20zm-1 17.9A8 8 0 0 1 4.2 10.2L9 15v1a2 2 0 0 0 2 2zm6.9-2.5A2 2 0 0 0 16 16h-1v-3a1 1 0 0 0-1-1H8v-2h2a1 1 0 0 0 1-1V7h2a2 2 0 0 0 2-2v-.4a8 8 0 0 1 2.9 12.8z"/></svg>
      WWW.TRV-GROUNDMAKRZ.COM
    </li>
  </ul>
</section>

<section class="card card--back">
  <div class="back-lockup">
    <div class="back-lockup__dot" aria-hidden="true"></div>
    <p class="back-lockup__name">TREVANE<br>GROUNDMAKRZ LLC</p>
    <p class="back-lockup__services">Land Clearing · Forestry Mulching · Excavation</p>
  </div>
</section>

</body>
</html>
```